Construction business card

I need a new business card, they can connect with my logo, brand.
What we do is residential house , design and build
I like: Navy blue / black
I attached our logo, brand,
and, some idea for business card.

```html
<!DOCTYPE html>
<html lang="en">
<head>
<meta charset="utf-8">
<title>Harlow Building Group – Business Card</title>
<link rel="stylesheet" href="https://fonts.googleapis.com/css2?family=Arimo:wght@400;700&display=swap">
<style>
  :root{
    --stage:#3a3a3a;
    --card:#232323;
    --card-edge:#1c1c1c;
    --mark:#141414;
    --mark-soft:#2e2e2e;
    --accent:#3a88cc;
    --white:#ffffff;
    --text:#f2f2f2;
  }
  *{margin:0;padding:0;box-sizing:border-box}
  html,body{width:1200px;height:900px;overflow:hidden}
  body{
    background:var(--stage);
    font-family:"Arimo",Arial,sans-serif;
    position:relative;
  }
  .card{
    position:absolute;
    left:260px;
    width:680px;
    height:390px;
    background:var(--card);
    border-radius:22px;
    overflow:hidden;
    box-shadow:0 14px 30px rgba(0,0,0,.45);
  }
  .card--back{top:40px}
  .card--front{top:470px}

  /* back */
  .brand-back{
    position:absolute;inset:0;
    display:flex;align-items:center;justify-content:center;gap:16px;
  }
  .brand-back__square{width:26px;height:26px;background:var(--mark)}
  .brand-back__name{
    font-weight:700;font-size:40px;letter-spacing:3px;
    color:var(--mark);text-transform:uppercase;
  }

  /* front */
  .brand-front{
    position:absolute;right:40px;top:70px;
    font-weight:700;font-size:44px;letter-spacing:2px;line-height:1;
    color:var(--mark-soft);text-transform:uppercase;text-align:right;
  }
  .wave{position:absolute;inset:0;width:100%;height:100%}
  .contact{
    position:absolute;left:48px;top:44px;color:var(--text);
  }
  .contact__name{
    font-weight:700;font-size:28px;color:var(--accent);letter-spacing:.5px;
  }
  .contact__role{font-size:17px;margin-top:2px}
  .contact__address{font-size:17px;line-height:1.3;margin-top:40px}
  .contact__list{list-style:none;margin-top:34px}
  .contact__item{
    display:flex;align-items:center;gap:10px;
    font-size:17px;line-height:1.55;
  }
  .contact__icon{width:15px;height:15px;fill:var(--accent);flex:none}
</style>
</head>
<body>

<section class="card card--back" aria-label="Card back">
  <div class="brand-back">
    <span class="brand-back__square"></span>
    <span class="brand-back__name">Harlow Building Group</span>
  </div>
</section>

<section class="card card--front" aria-label="Card front">
  <div class="brand-front">Harlow</div>

  <svg class="wave" viewBox="0 0 680 390" preserveAspectRatio="none" aria-hidden="true">
    <path d="M0,338 C210,330 390,318 520,250 C590,214 640,196 680,190 L680,390 L0,390 Z" fill="var(--white)"/>
    <path d="M0,350 C210,342 390,330 520,262 C590,226 640,210 680,206 L680,390 L0,390 Z" fill="#111"/>
    <path d="M0,354 C210,346 390,336 520,270 C590,234 640,218 680,214 L680,390 L0,390 Z" fill="var(--accent)"/>
  </svg>

  <div class="contact">
    <h1 class="contact__name">DANIEL CARTER</h1>
    <p class="contact__role">CEO/Founder</p>
    <p class="contact__address">27 Harrow Lane,<br>Westbury, VIC 3188</p>
    <ul class="contact__list">
      <li class="contact__item">
        <svg class="contact__icon" viewBox="0 0 24 24"><path d="M6.6 10.8a15.1 15.1 0 0 0 6.6 6.6l2.2-2.2c.3-.3.7-.4 1-.2 1.1.4 2.3.6 3.6.6.6 0 1 .4 1 1V20c0 .6-.4 1-1 1A17 17 0 0 1 3 4c0-.6.4-1 1-1h3.5c.6 0 1 .4 1 1 0 1.3.2 2.5.6 3.6.1.3 0 .7-.2 1z"/></svg>
        0400 555 018
      </li>
      <li class="contact__item">
        <svg class="contact__icon" viewBox="0 0 24 24"><path d="M2 5h20v14H2z M3.5 6.5l8.5 6.5 8.5-6.5" fill="var(--accent)" stroke="var(--card)" stroke-width="1.4"/></svg>
        hello@harlowbuild.com.au
      </li>
      <li class="contact__item">
        <svg class="contact__icon" viewBox="0 0 24 24"><circle cx="12" cy="12" r="10"/><path d="M2 12h20M12 2c3 3 3 17 0 20M12 2c-3 3-3 17 0 20" fill="none" stroke="var(--card)" stroke-width="1.4"/></svg>
        harlowbuild.com.au
      </li>
    </ul>
  </div>
</section>

</body>
</html>
```